Ferrow Hip Hop Dance Theater Flyer

Ferrow is a hip-hop dance theater company based in Los Angeles under the artistic direction of Lena “Reedowl” Marbury. Ferrow creates multimedia urban dance performances that incorporate street dance, poetry, theater, and film into provocative and daring performances. Speaking the language of Hip-Hop, Ferrow tells stories using the movement vocabulary of street dance styles including: bboying/bgirling, krump dance, house dance, locking, popping, waacking, and capoeira. Founded in 2007, Ferrow dancers represent the best in LA with extensive credits that include major films, TV shows, and music videos. Ferrow is committed to innovating the realm of hip-hop dance theater as well as uplifting the community through residencies, workshops, and special events.
Target Market(s)
Presenters- theater managers who might book our performances, event producers, middle and upper class parents who might hire Ferrow to perform at private events
Industry/Entity Type
Performing Art
Requirements
Must have
- Text/Copy as describe in word .doc "Ferrow General Flyer Copy"
- One main featured photo of multiple dancers with 2-3 secondary photos of single dancers and/or small groups of dancers.
- Clean, not-too-busy design
- Easy to read text
Nice to have
- A design similar in feel and layout to the "Old Ferrow Flyer" that's included for reference
- Use of bright neon green as an accent color
Should not have
- Lots of manipulation of the photographs

```html
<!DOCTYPE html>
<html lang="en">
<head>
<meta charset="utf-8">
<title>Ferrow Hip Hop Dance Theater Flyer</title>
<link href="https://fonts.googleapis.com/css2?family=Archivo+Black&family=Arimo:wght@400;700&display=swap" rel="stylesheet">
<style>
  :root {
    --neon: #8dc63f;
    --ink: #1b1b1b;
    --paper: #f4f4f4;
    --footer: #1f1d1d;
    --white: #ffffff;
    --rule: #3a3a3a;
  }
  * { margin: 0; padding: 0; box-sizing: border-box; }
  html, body { width: 846px; height: 1200px; overflow: hidden; }
  body { font-family: "Arimo", Arial, sans-serif; color: var(--ink); background: var(--paper); }
  .flyer { position: relative; width: 846px; height: 1200px; overflow: hidden; background: var(--paper); }
  .backdrop-photo {
    position: absolute; left: 0; top: 0; width: 846px; height: 1003px;
    background:
      radial-gradient(ellipse 260px 420px at 620px 420px, rgba(120,120,120,.28), transparent 70%),
      radial-gradient(ellipse 300px 220px at 300px 930px, rgba(140,140,140,.22), transparent 70%),
      linear-gradient(180deg, #ececec 0%, #e2e2e2 55%, #d9d9d9 100%);
  }
  .abs { position: absolute; }
  .brand-name {
    left: 118px; top: 58px; font-family: "Archivo Black", sans-serif;
    font-size: 64px; color: var(--neon); letter-spacing: 1px;
  }
  .headline {
    left: 385px; top: 40px; font-family: "Arimo", sans-serif; font-weight: 700;
    font-size: 39px; line-height: 42px; color: var(--ink); letter-spacing: -.3px;
  }
  .headline strong { font-family: "Archivo Black", sans-serif; font-weight: 400; }
  .pill {
    position: absolute; background: var(--neon); color: var(--white);
    font-family: "Archivo Black", sans-serif; font-size: 20px; letter-spacing: .5px;
    border-radius: 18px; display: flex; align-items: center; justify-content: center;
  }
  .site-pill { left: 385px; top: 135px; width: 420px; height: 33px; font-family: "Arimo", sans-serif; font-weight: 700; font-size: 21px; }
  .qmark { position: absolute; font-family: "Archivo Black", sans-serif; color: var(--neon); line-height: 1; }
  .qmark-inline { color: var(--neon); font-family: "Archivo Black", sans-serif; }
  .lead-quote { left: 123px; top: 192px; font-weight: 700; font-size: 16.5px; }
  .lead-credit { right: 128px; top: 216px; font-weight: 700; font-size: 16.5px; }
  .divider { left: 353px; top: 262px; width: 1.5px; height: 713px; background: var(--rule); }
  .about-pill { left: 52px; top: 262px; width: 230px; height: 32px; }
  .about-text {
    left: 52px; top: 310px; width: 279px; font-size: 15.6px; line-height: 22.2px; text-align: justify;
  }
  .offers-pill { left: 52px; top: 825px; width: 228px; height: 32px; }
  .offer-list { list-style: none; font-weight: 700; font-size: 16px; }
  .offer-list li { height: 25px; display: flex; align-items: center; }
  .offer-list li::before {
    content: ""; width: 8px; height: 8px; border-radius: 50%; background: var(--neon); margin-right: 7px;
  }
  .offers-left { left: 48px; top: 868px; }
  .offers-right { left: 195px; top: 868px; }
  .rep-pill { left: 372px; top: 262px; width: 205px; height: 32px; }
  .work-title { font-family: "Archivo Black", sans-serif; font-size: 19.5px; left: 382px; }
  .work-text { left: 382px; width: 415px; font-size: 15.6px; line-height: 22.2px; text-align: justify; }
  .review { left: 422px; width: 373px; font-size: 15.6px; line-height: 22.2px; text-align: justify; }
  .review-credit { font-weight: 700; font-size: 16px; }
  .footer { position: absolute; left: 0; top: 1003px; width: 846px; height: 197px; background: var(--footer); }
  .booking-pill { left: 52px; top: 1033px; width: 170px; height: 32px; }
  .contact-pill { left: 470px; top: 1033px; width: 167px; height: 32px; }
  .contact-block { color: var(--white); font-weight: 700; font-size: 16.5px; }
  .contact-block .name { height: 25px; padding-left: 24px; }
  .contact-block .row { height: 25px; display: flex; align-items: center; }
  .contact-block svg { width: 15px; height: 15px; margin-right: 9px; flex: none; }
</style>
</head>
<body>
<main class="flyer">
  <div class="backdrop-photo" role="img" aria-label="Faded black-and-white photo of a hip-hop dancer in motion behind the page content"></div>

  <div class="abs brand-name">Ferrow</div>
  <h1 class="abs headline">MULTIMEDIA <strong>HIP-HOP</strong><br><strong>DANCE</strong> THEATER</h1>
  <div class="pill site-pill">www.FerrowPerformance.com</div>

  <span class="qmark" style="left:68px; top:182px; font-size:64px;">“</span>
  <p class="abs lead-quote">Reclaiming hip-hop… by expanding the idiom’s creative horizons…</p>
  <p class="abs lead-credit">-Coastline Herald</p>
  <span class="qmark" style="left:728px; top:182px; font-size:64px;">”</span>

  <div class="abs divider"></div>

  <h2 class="pill about-pill">ABOUT FERROW</h2>
  <p class="abs about-text">Ferrow is a hip-hop dance theater company based in Los Angeles under the artistic direction of Lena “Reedowl” Marbury. Ferrow creates multimedia urban dance performances that incorporate street dance, poetry, theater, and film into provocative and daring performances. Speaking the language of Hip-Hop, Ferrow tells stories using the movement vocabulary of street dance styles including: bboying/bgirling, krump dance, house dance, locking, popping, waacking, and capoeira. Founded in 2007, Ferrow dancers represent the best in LA with extensive credits that include major films, TV shows, and music videos. Ferrow is committed to innovating the realm of hip-hop dance theater as well as uplifting the community through residencies, workshops, and special events.</p>

  <h2 class="pill offers-pill">FERROW OFFERS</h2>
  <ul class="abs offer-list offers-left">
    <li>Performances</li><li>School Shows</li><li>Street Shows</li><li>Residencies</li>
  </ul>
  <ul class="abs offer-list offers-right">
    <li>Workshops</li><li>Classes</li><li>Private Events</li>
  </ul>

  <h2 class="pill rep-pill">REPERTORY</h2>

  <h3 class="abs work-title" style="top:307px;">Lacebound Stories</h3>
  <p class="abs work-text" style="top:344px;">Lacebound Stories is a performance collaboration between Ferrow and story architect Theo Valdran featuring 10 dancers, spoken word poetry, and 5 short films with original generation B-Boys. Through the virtuosity and hyper-physicality of street dance, Ferrow confronts themes of poverty, violence, globalization, diversity, and family. Lacebound Stories tells the stories of sneakers: of those who make them, those who wear them, and those who dance in them.</p>
  <span class="qmark" style="left:378px; top:556px; font-size:56px;">“</span>
  <p class="abs review" style="top:562px;">The thrilling group choreography… suggested solidarity in the streets, a sense that the b-boy/ b-girl community itself lifts its members toward loftier horizons even as they contort their bodies upside down. <span class="qmark-inline">”</span></p>
  <p class="abs review-credit" style="right:64px; top:653px;">-Stage Motion Review</p>

  <h3 class="abs work-title" style="top:694px;">Clay Tablet Chronicles</h3>
  <p class="abs work-text" style="top:726px;">Ferrow blurs the lines between the past and present with their vibrant interpretation of The Epic of Gilgamesh. Ten dancers portray key characters from this ancient Mesopotamian poem, which follows King Gilgamesh as he struggles to reconcile with mortality and understand the meaning of life.</p>
  <span class="qmark" style="left:378px; top:868px; font-size:56px;">“</span>
  <p class="abs review" style="top:874px;">“The vision for ancient myths has been owned for decades by the ferocious Marian Holloway… Yet Marbury, seized a piece of that sacred territory with the debut of ‘Clay Tablet Chronicles. <span class="qmark-inline">”</span></p>
  <p class="abs review-credit" style="right:50px; top:963px;">-Coastline Herald</p>

  <footer class="footer"></footer>
  <h2 class="pill booking-pill">BOOKING</h2>
  <h2 class="pill contact-pill">CONTACT</h2>

  <div class="abs contact-block" style="left:52px; top:1075px;">
    <div class="name">Dana Whitlock, Meridian Arts Network</div>
    <div class="row"><svg viewBox="0 0 16 16"><circle cx="8" cy="8" r="6.5" fill="none" stroke="#8dc63f" stroke-width="1.8"/><path d="M1.5 8h13M8 1.5c-3 3.5-3 9.5 0 13M8 1.5c3 3.5 3 9.5 0 13" fill="none" stroke="#8dc63f" stroke-width="1.3"/></svg>MeridianArts.com</div>
    <div class="row"><svg viewBox="0 0 16 16"><circle cx="8" cy="8" r="6.8" fill="none" stroke="#8dc63f" stroke-width="1.5"/><path d="M5.3 4.5l1.4-.4 1 2-1 .8c.5 1 1.2 1.8 2.2 2.3l.8-1 2 1-.4 1.4c-3 .3-6.4-3-6-6.1z" fill="#8dc63f"/></svg>310-555-0147</div>
    <div class="row"><svg viewBox="0 0 16 16"><rect x="1.5" y="3.5" width="13" height="9" fill="#8dc63f"/><path d="M1.5 3.5l6.5 5 6.5-5" fill="none" stroke="#1f1d1d" stroke-width="1.2"/></svg>Dana@MeridianArts.com</div>
  </div>

  <div class="abs contact-block" style="left:474px; top:1075px;">
    <div class="name">Lena Marbury, Ferrow Artistic Director</div>
    <div class="row"><svg viewBox="0 0 16 16"><circle cx="8" cy="8" r="6.5" fill="none" stroke="#8dc63f" stroke-width="1.8"/><path d="M1.5 8h13M8 1.5c-3 3.5-3 9.5 0 13M8 1.5c3 3.5 3 9.5 0 13" fill="none" stroke="#8dc63f" stroke-width="1.3"/></svg>FerrowPerformance.com</div>
    <div class="row"><svg viewBox="0 0 16 16"><circle cx="8" cy="8" r="6.8" fill="none" stroke="#8dc63f" stroke-width="1.5"/><path d="M5.3 4.5l1.4-.4 1 2-1 .8c.5 1 1.2 1.8 2.2 2.3l.8-1 2 1-.4 1.4c-3 .3-6.4-3-6-6.1z" fill="#8dc63f"/></svg>213-555-0182</div>
    <div class="row"><svg viewBox="0 0 16 16"><rect x="1.5" y="3.5" width="13" height="9" fill="#8dc63f"/><path d="M1.5 3.5l6.5 5 6.5-5" fill="none" stroke="#1f1d1d" stroke-width="1.2"/></svg>Info@FerrowPerformance.com</div>
  </div>
</main>
</body>
</html>
```